2022 Landscaping Services

Please use the prior year design as an example. Similar style but DO NOT COPY IT EXACTLY- you can use different photos from our website if you like. Same text for year 2022.
Design should clearly depict the differences between the 3 products so people can buy one of them. Be creative!

size 8.5" x 11"

Must provide source file in photoshop if you are winner

Requirements
Must have
• Same text as original flier but with year 2022

```html
<!DOCTYPE html>
<html lang="en">
<head>
<meta charset="utf-8">
<title>Maplewood Cemetery – 2022 Gravesite Landscaping Packages</title>
<link rel="stylesheet" href="https://fonts.googleapis.com/css2?family=Montserrat:wght@500;600;700;800&family=Cormorant+Garamond:wght@500&display=swap">
<style>
  :root{
    --maroon:#7a1f2e;
    --maroon-dark:#5e1521;
    --orange:#e39a3b;
    --gray:#6d6e70;
    --gray-dark:#555658;
    --shade:#ececec;
    --line:#d6d6d6;
    --ink:#3a3a3a;
    --white:#ffffff;
    --page:#f0f0f0;
  }
  *{box-sizing:border-box;margin:0;padding:0}
  html,body{width:783px;height:1200px;overflow:hidden;background:var(--page)}
  body{font-family:"Montserrat",Arial,sans-serif;color:var(--ink)}
  .flyer{position:absolute;left:0;top:47px;width:783px;height:1105px;background:var(--white);overflow:hidden}

  .hero{position:absolute;left:0;top:0;width:783px;height:460px}
  .brand{position:absolute;left:50px;top:60px;display:flex;align-items:center;gap:10px;
    font-weight:600;font-size:26px;letter-spacing:.5px;color:var(--maroon)}
  .brand__dot{width:16px;height:16px;border-radius:50%;background:var(--maroon)}

  .title{position:absolute;left:49px;top:165px;color:var(--white);line-height:1}
  .title__year{font-family:"Cormorant Garamond",Georgia,serif;font-weight:500;font-size:76px;color:var(--orange);letter-spacing:-1px}
  .title__line{font-weight:700;letter-spacing:-.5px}
  .title__line--1{font-size:40px;margin-top:2px}
  .title__line--2{font-size:46px;margin-top:4px}
  .title__line--3{font-size:62px;font-weight:800;margin-top:2px}

  .plans{position:absolute;left:0;top:468px;width:783px;height:67px}
  .plans__tab{position:absolute;left:49px;top:14px;color:var(--white);font-weight:700;font-size:20px;line-height:20px}
  .plans__name{position:absolute;top:16px;width:180px;margin-left:-90px;text-align:center;color:var(--white);line-height:1}
  .plans__name b{display:block;font-weight:600;font-size:18px}
  .plans__name span{display:block;font-weight:500;font-size:12px;margin-top:5px}
  .plans__name--seasonal{left:337px}
  .plans__name--basic{left:506px}
  .plans__name--perpetual{left:679px;top:22px}
  .badge{position:absolute;left:572px;top:-32px;width:60px;height:60px;border-radius:50%;
    background:var(--orange);border:3px solid var(--white);color:var(--white);
    display:flex;flex-direction:column;align-items:center;justify-content:center;line-height:1}
  .badge b{font-size:10px;font-weight:600}
  .badge span{font-size:7px;font-weight:600}

  .table{position:absolute;left:0;top:535px;width:783px;display:grid;
    grid-template-columns:245px 179px 165px 194px;
    grid-template-rows:72px 48px 52px 47px 54px 48px 52px 112px}
  .cell{display:flex;align-items:center;justify-content:center;text-align:center;border-left:1px solid var(--line)}
  .cell--label{justify-content:flex-start;text-align:left;padding-left:49px;border-left:none;
    font-weight:700;font-size:14px;line-height:17px;color:var(--ink)}
  .row-shade{background:var(--shade)}
  .cell--perpetual.row-shade{background:var(--maroon);border-left-color:var(--maroon)}
  .cell--perpetual{border-left:none}
  .cell--note{font-weight:700;font-size:10px;line-height:12.5px;padding:0 14px}

  .icon{width:17px;height:17px}
  .price{flex-direction:column;line-height:1.2}
  .price--row{background:var(--shade)}
  .price--perpetual{background:var(--gray);color:var(--white);border-left:none}
  .price__multi{font-weight:700;font-size:13px;color:var(--maroon)}
  .price__years{font-weight:600;font-size:10px;margin-top:4px}
  .price__lock{font-weight:700;font-size:9.5px;margin-top:9px;line-height:12px}
  .price__amount{font-weight:700;font-size:27px;color:var(--maroon)}
  .price--perpetual .price__amount{color:var(--white)}
  .price__terms{font-weight:700;font-size:9.5px;line-height:12px;margin-top:6px;padding:0 22px}

  .footer{position:absolute;left:0;top:1030px;width:783px;height:75px;background:var(--maroon);
    color:var(--white);display:flex;align-items:center;padding-left:49px}
  .footer__item{display:flex;align-items:center;gap:9px}
  .footer__phone{font-weight:700;font-size:22px;letter-spacing:.3px}
  .footer__text{font-weight:500;font-size:13.5px;line-height:17px}
  .footer__sep{width:0;height:38px;border-left:1px dashed rgba(255,255,255,.55);margin:0 13px}
</style>
</head>
<body>
<main class="flyer">

  <svg class="hero" viewBox="0 0 783 460" aria-hidden="false">
    <defs>
      <linearGradient id="foliage" x1="0" y1="0" x2="1" y2="1">
        <stop offset="0" stop-color="#8a2230"/>
        <stop offset=".5" stop-color="#6e1a26"/>
        <stop offset="1" stop-color="#4d1119"/>
      </linearGradient>
      <linearGradient id="dusk" x1="0" y1="0" x2="1" y2="1">
        <stop offset="0" stop-color="#3d3a22"/>
        <stop offset=".35" stop-color="#a98a4a"/>
        <stop offset=".6" stop-color="#4a4a44"/>
        <stop offset="1" stop-color="#1c1d1a"/>
      </linearGradient>
    </defs>
    <rect width="783" height="130" fill="#ffffff"/>
    <rect y="130" width="783" height="323" fill="url(#foliage)" role="img" aria-label="Autumn trees with deep red foliage"/>
    <polygon points="585,0 598,0 478,122 465,122" fill="#7a1f2e"/>
    <polygon points="640,0 700,0 783,90 783,360 690,453 575,453 372,250"
             fill="url(#dusk)" stroke="#ffffff" stroke-width="14" stroke-linejoin="miter"
             role="img" aria-label="Tree-lined cemetery path at sunset"/>
    <polygon points="783,362 783,460 685,460" fill="#ffffff"/>
    <line x1="790" y1="392" x2="727" y2="455" stroke="#7a1f2e" stroke-width="7"/>
    <rect x="0" y="453" width="560" height="3" fill="#555658"/>
  </svg>

  <div class="brand"><span class="brand__dot"></span>Maplewood Cemetery</div>

  <h1 class="title">
    <div class="title__year">2022</div>
    <div class="title__line title__line--1">GRAVESITE</div>
    <div class="title__line title__line--2">LANDSCAPING</div>
    <div class="title__line title__line--3">PACKAGES</div>
  </h1>

  <header class="plans">
    <svg width="783" height="67" viewBox="0 0 783 67" style="position:absolute;left:0;top:0">
      <rect width="783" height="67" fill="#6d6e70"/>
      <path d="M0 0 H220 C232 22 238 48 250 67 H0 Z" fill="#7a1f2e"/>
    </svg>
    <div class="plans__tab">SERVICES<br>OFFERED</div>
    <div class="plans__name plans__name--seasonal"><b>SEASONAL</b><span>CARE ENDOWMENT</span></div>
    <div class="plans__name plans__name--basic"><b>BASIC</b><span>CARE ENDOWMENT</span></div>
    <div class="plans__name plans__name--perpetual"><b>PERPETUAL</b><span>CARE ENDOWMENT</span></div>
    <div class="badge"><b>MOST</b><span>POPULAR</span></div>
  </header>

  <svg width="0" height="0" style="position:absolute">
    <symbol id="tick" viewBox="0 0 20 20"><circle cx="10" cy="10" r="9" fill="currentColor"/><path d="M5.8 10.3l2.8 2.8 5.6-5.8" fill="none" stroke="var(--check,#fff)" stroke-width="2.2" stroke-linecap="round" stroke-linejoin="round"/></symbol>
    <symbol id="none" viewBox="0 0 20 20"><circle cx="10" cy="10" r="8" fill="none" stroke="#3a3a3a" stroke-width="1.6"/><path d="M4.5 15.5L15.5 4.5" stroke="#3a3a3a" stroke-width="1.6"/></symbol>
  </svg>

  <section class="table">
    <div class="cell cell--label">Weeding &amp; Trimming<br>On Your Gravesite</div>
    <div class="cell cell--note">Approximately every 7 weeks during the growing season: Mid-April through Mid-October</div>
    <div class="cell cell--note">2 times per year:<br>Mid-May<br>Mid-September</div>
    <div class="cell cell--note cell--perpetual">Approximately every 7 weeks during the growing season: Mid-April through Mid-October</div>

    <div class="cell cell--label row-shade">Payment Ensured<br>Forever Grave Care</div>
    <div class="cell row-shade"><svg class="icon"><use href="#none"/></svg></div>
    <div class="cell row-shade"><svg class="icon" style="color:var(--maroon)"><use href="#tick"/></svg></div>
    <div class="cell cell--perpetual row-shade"><svg class="icon" style="color:#fff;--check:#7a1f2e"><use href="#tick"/></svg></div>

    <div class="cell cell--label">Monument Leveling</div>
    <div class="cell"><svg class="icon"><use href="#none"/></svg></div>
    <div class="cell"><svg class="icon" style="color:var(--maroon)"><use href="#tick"/></svg></div>
    <div class="cell cell--perpetual"><svg class="icon" style="color:var(--maroon)"><use href="#tick"/></svg></div>

    <div class="cell cell--label row-shade">Monument Cleaning</div>
    <div class="cell row-shade"><svg class="icon"><use href="#none"/></svg></div>
    <div class="cell row-shade"><svg class="icon"><use href="#none"/></svg></div>
    <div class="cell cell--perpetual row-shade"><svg class="icon" style="color:#fff;--check:#7a1f2e"><use href="#tick"/></svg></div>

    <div class="cell cell--label">Full Bed Of Boxwood<br>Shrubs</div>
    <div class="cell"><svg class="icon"><use href="#none"/></svg></div>
    <div class="cell"><svg class="icon"><use href="#none"/></svg></div>
    <div class="cell cell--perpetual"><svg class="icon" style="color:var(--maroon)"><use href="#tick"/></svg></div>

    <div class="cell cell--label row-shade">Replacement Of Shrubs</div>
    <div class="cell row-shade"><svg class="icon"><use href="#none"/></svg></div>
    <div class="cell row-shade"><svg class="icon"><use href="#none"/></svg></div>
    <div class="cell cell--perpetual row-shade"><svg class="icon" style="color:#fff;--check:#7a1f2e"><use href="#tick"/></svg></div>

    <div class="cell cell--label">Trust Certificate</div>
    <div class="cell"><svg class="icon"><use href="#none"/></svg></div>
    <div class="cell"><svg class="icon"><use href="#none"/></svg></div>
    <div class="cell cell--perpetual"><svg class="icon" style="color:var(--maroon)"><use href="#tick"/></svg></div>

    <div class="cell cell--label price--row">Valid through<br>10/31/22</div>
    <div class="cell price price--row">
      <div class="price__multi">$357 | $238 | $119</div>
      <div class="price__years">3 Years | 2 Years | 1 Year</div>
      <div class="price__lock">Multi-year payment locks<br>in current rates</div>
    </div>
    <div class="cell price price--row">
      <div class="price__amount">$255</div>
      <div class="price__terms">12 Monthly payments. Call for single payment discounts.</div>
    </div>
    <div class="cell price price--perpetual">
      <div class="price__amount">$313</div>
      <div class="price__terms">12 Monthly payments. Call for single payment discounts.</div>
    </div>
  </section>

  <footer class="footer">
    <div class="footer__item">
      <svg width="20" height="20" viewBox="0 0 24 24"><path d="M6.6 2.5l3 3.4-1.8 2.6c1.2 2.7 3.2 4.8 5.8 6l2.6-1.8 3.4 3-1.6 3.4C10.6 19.6 4.4 13.4 3.2 4.1z" fill="none" stroke="#e39a3b" stroke-width="2" stroke-linejoin="round"/></svg>
      <span class="footer__phone">(555) 014-2290</span>
    </div>
    <span class="footer__sep"></span>
    <div class="footer__item">
      <svg width="14" height="19" viewBox="0 0 14 19"><path d="M7 0C3.1 0 0 3.1 0 7c0 5 7 12 7 12s7-7 7-12c0-3.9-3.1-7-7-7z" fill="#e39a3b"/><circle cx="7" cy="7" r="2.6" fill="#7a1f2e"/></svg>
      <span class="footer__text">48 Orchard Ln.<br>Fairview, NJ 07000</span>
    </div>
    <span class="footer__sep"></span>
    <div class="footer__item">
      <svg width="15" height="15" viewBox="0 0 20 20" fill="none" stroke="#e39a3b" stroke-width="1.6"><circle cx="10" cy="10" r="8.5"/><ellipse cx="10" cy="10" rx="3.6" ry="8.5"/><path d="M1.5 10h17M3 5.5h14M3 14.5h14"/></svg>
      <span class="footer__text">www.maplewoodcemetery.org</span>
    </div>
  </footer>

</main>
</body>
</html>
```